Ridgeline Orchards Organic Cherry POS card 7x11

We are wanting to create a one-sided 7 x 11 organic cherry card that is eye catching and informative.This should be clear and easy to read and not cluttered. We use these cards as a display in grocery stores, demo stands, and other events to market Organic Ridgeline Sweet Orchards. We have a few facts that we would like displayed on the card (see attachment).

Target Market(s)

Consumers

Industry/Entity Type

Agriculture

Requirements
Must have
• Natural color palettes
• Easy to read
• Ridgeline Orchards
Nice to have
• Unique, realistic cherry design

```html
<!DOCTYPE html>
<html lang="en">
<head>
<meta charset="utf-8">
<title>Ridgeline Orchards – Organic Cherry Card</title>
<link rel="stylesheet" href="https://fonts.googleapis.com/css2?family=Josefin+Sans:wght@600&family=Kaushan+Script&display=swap">
<style>
  :root {
    --page: #ffffff;
    --tan: #a38e72;
    --mauve: #7a5350;
    --plum: #5e3234;
    --cherry: #6e1620;
    --cherry-deep: #3d0a12;
    --ink: #33201d;
    --cream: #f7f1ea;
    --frame: rgba(236, 220, 214, 0.6);
  }
  * { margin: 0; padding: 0; box-sizing: border-box; }
  html, body { width: 1200px; height: 880px; overflow: hidden; background: var(--page); }
  .card {
    position: absolute; left: 0; top: 58px; width: 1200px; height: 764px; overflow: hidden;
  }
  .card__photo {
    position: absolute; inset: 0;
    background:
      radial-gradient(ellipse 150px 170px at 960px 430px, var(--cherry-deep) 0%, rgba(61,10,18,0) 100%),
      radial-gradient(ellipse 170px 190px at 740px 460px, var(--cherry) 0%, rgba(110,22,32,0.5) 60%, rgba(110,22,32,0) 100%),
      radial-gradient(ellipse 420px 260px at 1050px 60px, rgba(190,170,130,0.8) 0%, rgba(190,170,130,0) 100%),
      linear-gradient(180deg, var(--tan) 0%, var(--mauve) 45%, var(--plum) 100%);
  }
  .brand {
    position: absolute; left: 0; right: 0; top: 52px;
    display: flex; justify-content: center; align-items: center; gap: 16px;
    font-family: "Josefin Sans", sans-serif; font-weight: 600;
    font-size: 38px; letter-spacing: 0.08em; color: var(--cream);
  }
  .brand__dot { width: 30px; height: 30px; border-radius: 50%; border: 2px solid var(--cream); }
  .frame { position: absolute; left: 0; top: 0; }
  .facts {
    position: absolute; left: 52px; top: 196px;
    font-family: "Josefin Sans", sans-serif; font-weight: 600;
    font-size: 29px; letter-spacing: 0.3em; color: var(--ink);
    text-transform: uppercase; line-height: 44px;
  }
  .facts p + p { margin-top: 14px; }
  .benefits {
    position: absolute; left: 764px; top: 407px; width: 280px; height: 280px;
    border: 3px solid rgba(255,255,255,0.45); border-radius: 50%;
  }
  .benefits__list {
    position: absolute; left: 700px; top: 416px; width: 400px;
    font-family: "Kaushan Script", cursive; font-size: 21px; color: var(--cream);
    list-style: none; text-align: center; line-height: 43px;
  }
</style>
</head>
<body>
  <main class="card">
    <div class="card__photo" role="img" aria-label="Photograph of two glossy wet dark red cherries hanging from green stems against a soft blurred brown background"></div>

    <header class="brand">
      <span class="brand__dot"></span>
      <span class="brand__name">Ridgeline Orchards</span>
    </header>

    <svg class="frame" width="1200" height="764" viewBox="0 0 1200 764" aria-hidden="true">
      <rect x="20" y="160" width="1158" height="559" fill="none" stroke="var(--frame)" stroke-width="4" stroke-dasharray="22 14"/>
    </svg>

    <section class="facts">
      <p>Organic<br>Ridgeline Orchards</p>
      <p>Make up 1/3</p>
      <p>of the nation's<br>production.</p>
      <p>Washington State<br>is the nation's<br>largest producer<br>&nbsp;of organic<br>cherries.</p>
    </section>

    <div class="benefits"></div>
    <ul class="benefits__list">
      <li>Health benefits:</li>
      <li>fat free</li>
      <li>source of vitamin C</li>
      <li>a natural anti-inflammatory</li>
      <li>source of potassium</li>
      <li>source of melatonin</li>
    </ul>
  </main>
</body>
</html>
```